Boutique Technology Consultancy specialising is Electronic and physical security

We need to redo our existing outdated website. For your reference the link www.pelu.com.au

```html
<!DOCTYPE html>
<html lang="en">
<head>
<meta charset="utf-8">
<title>Pelu Services</title>
<link href="https://fonts.googleapis.com/css2?family=Figtree:wght@400;500;600&family=Montserrat:wght@400;500;600&display=swap" rel="stylesheet">
<style>
:root{
  --red:#d62b26;
  --red-dark:#c0221d;
  --ink:#222;
  --text:#333;
  --charcoal:#2a2a2a;
  --footer:#111;
  --white:#fff;
  --card-border:#e2e2e2;
}
*{box-sizing:border-box;margin:0;padding:0}
html,body{width:1200px;height:3843px;overflow:hidden}
body{position:relative;background:var(--white);font-family:"Montserrat",sans-serif;color:var(--text)}
.heading{font-family:"Figtree",sans-serif;font-weight:500;text-transform:uppercase}
.btn{position:absolute;background:var(--red);color:var(--white);font-family:"Figtree",sans-serif;font-weight:500;font-size:23px;display:flex;align-items:center;justify-content:center;text-transform:uppercase;white-space:nowrap}

/* header */
.site-header{position:absolute;left:0;top:0;width:1200px;height:97px;background:var(--white)}
.brand{position:absolute;left:112px;top:22px;display:flex;align-items:center;gap:12px}
.brand-square{width:22px;height:22px;background:var(--red)}
.brand-name{font-family:"Figtree",sans-serif;font-weight:600;font-size:44px;color:var(--ink);letter-spacing:1px}
.main-nav{position:absolute;top:38px;right:112px;display:flex;gap:37px;font-family:"Figtree",sans-serif;font-size:17px;color:#333}
.main-nav .active{color:var(--red)}

/* hero */
.hero{position:absolute;left:0;top:97px;width:1200px;height:515px;background:linear-gradient(100deg,#b5575b 0%,#c46a6c 45%,#9f4b4f 75%,#6e3437 100%)}
.hero-title{position:absolute;left:110px;top:143px;font-family:"Figtree",sans-serif;font-weight:500;font-size:47px;line-height:66px;color:var(--white);text-transform:uppercase}

/* section titles */
.section-title{position:absolute;left:0;width:1200px;text-align:center;font-size:37px;color:var(--red)}
.section-title span::before,.section-title span::after{content:"";display:inline-block;width:38px;height:3px;background:currentColor;vertical-align:middle;margin:0 14px}
.intro{position:absolute;left:195px;width:810px;text-align:center;font-size:16px;line-height:32px;color:#333}

/* experience cards */
.card{position:absolute;top:907px;width:327px;height:430px;background:var(--white);border:1px solid var(--card-border);border-radius:8px;box-shadow:0 2px 6px rgba(0,0,0,.12)}
.card-photo{position:absolute;left:8px;top:9px;width:311px;height:215px;border-radius:6px}
.card-title{position:absolute;left:22px;top:260px;font-size:22px;color:var(--red);white-space:nowrap}
.card-text{position:absolute;left:23px;top:300px;width:290px;height:64px;overflow:hidden;font-size:15.5px;line-height:32px;color:#333}
.card-link{position:absolute;left:23px;top:373px;font-family:"Figtree",sans-serif;font-size:19px;color:var(--red);text-decoration:underline;display:flex;align-items:center;gap:8px}

/* chevron bullet */
.chev::before{content:"";display:inline-block;width:0;height:0;border-left:8px solid currentColor;border-top:4px solid transparent;border-bottom:4px solid transparent;margin-right:14px;vertical-align:1px}

/* about */
.about{position:absolute;left:0;top:1533px;width:1200px;height:513px;background:var(--charcoal)}
.about-photo{position:absolute;left:115px;top:90px;width:390px;height:330px;background:linear-gradient(160deg,#8fa6b8 0%,#4b5660 50%,#1c1c1c 100%)}
.about-title{position:absolute;left:601px;top:55px;font-size:35px;color:var(--white);white-space:nowrap}
.about-title::before,.about-title::after{content:"";display:inline-block;width:38px;height:3px;background:var(--white);vertical-align:middle;margin:0 14px}
.about-title::before{margin-left:0}
.about-text{position:absolute;left:601px;top:130px;width:470px;font-size:16px;line-height:32px;color:var(--white)}
.about-list{position:absolute;left:647px;top:242px;list-style:none;font-size:16px;line-height:39px;color:var(--white)}
.about-list li{margin-left:-22px}

/* services */
.services{position:absolute;left:0;top:2046px;width:1200px;height:808px;background:linear-gradient(90deg,#6a7b8c 0%,#9aa8b4 25%,#d9dde1 45%,#f7f2f2 60%,#fff 80%)}
.services-title{position:absolute;left:583px;top:38px;font-size:35px;color:var(--red)}
.services-title::after{content:"";position:absolute;left:0;top:50px;width:38px;height:3px;background:var(--red)}
.services-text{position:absolute;left:584px;top:124px;width:510px;font-size:15.5px;line-height:32px;color:#333}
.service-box{position:absolute;left:583px;width:480px;height:172px;background:linear-gradient(90deg,var(--red) 0%,#e0504b 45%,rgba(230,120,120,.3) 90%,rgba(255,255,255,0) 100%);border-radius:6px 0 0 6px}
.service-box h3{position:absolute;left:66px;top:18px;font-family:"Figtree",sans-serif;font-weight:500;font-size:23px;color:var(--white);white-space:nowrap}
.service-box ul{position:absolute;left:66px;top:64px;list-style:none;font-size:15.5px;line-height:34px;color:var(--white);font-weight:500;white-space:nowrap}
.service-icon{position:absolute;left:396px;top:50px;width:72px;height:72px;border-radius:50%;background:var(--white);box-shadow:0 2px 8px rgba(0,0,0,.15);display:flex;align-items:center;justify-content:center}

/* team */
.team-card{position:absolute;text-align:center}
.team-card.featured{background:var(--white);box-shadow:0 2px 10px rgba(0,0,0,.18)}
.team-photo{width:120px;height:120px;border-radius:50%;margin:0 auto;background:linear-gradient(160deg,#d9c7bb,#8b7a70)}
.team-name{font-family:"Figtree",sans-serif;font-weight:500;font-size:23px;color:var(--red);text-transform:uppercase;margin-top:26px}
.team-role{font-family:"Figtree",sans-serif;font-weight:500;font-size:21px;line-height:36px;color:#333;margin-top:2px}
.team-bio{font-size:16px;line-height:32px;color:#333;margin-top:14px}
.arrow{position:absolute;width:44px;height:44px;border-radius:50%;background:var(--red);display:flex;align-items:center;justify-content:center}

/* footer */
.site-footer{position:absolute;left:0;top:3519px;width:1200px;height:324px;background:var(--footer);color:var(--white)}
.footer-brand{position:absolute;left:142px;top:60px;display:flex;align-items:center;gap:12px}
.footer-brand .brand-name{color:var(--white)}
.socials{position:absolute;left:143px;top:161px;display:flex;gap:10px}
.socials span{width:30px;height:30px;background:var(--white)}
.socials span:nth-child(2){background:var(--red)}
.footer-head{position:absolute;top:54px;font-family:"Figtree",sans-serif;font-weight:500;font-size:23px}
.footer-links{position:absolute;top:112px;left:470px;display:grid;grid-template-columns:155px 120px;row-gap:17px;font-size:16px;line-height:22px}
.contact-list{position:absolute;left:847px;top:104px;font-size:16px;line-height:39px;list-style:none}
.footer-rule{position:absolute;left:140px;top:275px;width:890px;height:1px;background:#444}
.copyright{position:absolute;left:0;top:293px;width:1200px;text-align:center;font-size:12.5px}
</style>
</head>
<body>

<header class="site-header">
  <div class="brand"><span class="brand-square"></span><span class="brand-name">PELU</span></div>
  <nav class="main-nav">
    <span class="active">HOME</span><span>EXPERIENCE</span><span>SERVICES</span><span>TEAM</span><span>ABOUT</span><span>CONTACT</span>
  </nav>
</header>

<section class="hero" role="img" aria-label="Two business colleagues reviewing a tablet in an office, tinted red">
  <h1 class="hero-title">Your technology<br>projects made<br>easy.</h1>
</section>

<h2 class="section-title heading" style="top:688px"><span>Experience</span></h2>
<p class="intro" style="top:759px">Pelu has a diverse range of project experience across a range of industries within both the public and private sectors. The following is a small sample of some of the clients and sites we have worked with.</p>

<article class="card" style="left:100px">
  <div class="card-photo" role="img" aria-label="Glass cone roof above a historic brick tower" style="background:linear-gradient(135deg,#3b4550,#8e9aa6 50%,#6a4d3c)"></div>
  <h3 class="card-title heading">Harbour Central</h3>
  <p class="card-text">Security technology design consulting for this popular retail precinct.</p>
  <span class="card-link">READ MORE <svg width="24" height="12" viewBox="0 0 24 12"><path d="M0 6h22M16 1l6 5-6 5" fill="none" stroke="currentColor" stroke-width="1.8"/></svg></span>
</article>
<article class="card" style="left:436px">
  <div class="card-photo" role="img" aria-label="Concrete motorway bridge over a river with hills behind" style="background:linear-gradient(180deg,#6f7e88,#8a9090 50%,#5e5a50)"></div>
  <h3 class="card-title heading">Ridgeway Link</h3>
  <p class="card-text">Virtual servers, network and CCTV upgrade design and project delivery.</p>
  <span class="card-link">READ MORE <svg width="24" height="12" viewBox="0 0 24 12"><path d="M0 6h22M16 1l6 5-6 5" fill="none" stroke="currentColor" stroke-width="1.8"/></svg></span>
</article>
<article class="card" style="left:770px">
  <div class="card-photo" role="img" aria-label="Ornate heritage hospital facade with balconies" style="background:linear-gradient(180deg,#6b8fc4,#c5874f 35%,#a65a32)"></div>
  <h3 class="card-title heading">Clare Women's Hospital</h3>
  <p class="card-text">Security technology lifecycle consulting for this leading Health provider.</p>
  <span class="card-link">READ MORE <svg width="24" height="12" viewBox="0 0 24 12"><path d="M0 6h22M16 1l6 5-6 5" fill="none" stroke="currentColor" stroke-width="1.8"/></svg></span>
</article>

<a class="btn" style="left:436px;top:1388px;width:328px;height:60px">More about experience</a>

<section class="about">
  <div class="about-photo" role="img" aria-label="Construction workers silhouetted on steel scaffolding against the sky"></div>
  <h2 class="about-title heading">About us</h2>
  <p class="about-text">Pelu Services was established in 2016 by Dan Harlow to provide technology consulting services to corporate and government clients with a focus on:</p>
  <ul class="about-list">
    <li class="chev">Property/facilities management</li>
    <li class="chev">Asset management</li>
    <li class="chev">Development and Construction</li>
  </ul>
  <a class="btn" style="left:601px;top:389px;width:243px;height:60px">Learn more Pelu</a>
</section>

<section class="services" role="img" aria-label="Senior consultant with glasses working on a laptop, fading into white">
  <h2 class="services-title heading">Services</h2>
  <p class="services-text">Pelu Services provides independent professional services for projects as well as operations and maintenance. We offer end to end services</p>
  <div class="service-box" style="top:263px">
    <h3>STRATEGY</h3>
    <ul><li class="chev">Technology roadmaps</li><li class="chev">Master standards</li><li class="chev">Asset management plans</li></ul>
    <div class="service-icon"><svg width="40" height="40" viewBox="0 0 40 40" fill="none" stroke="#d62b26" stroke-width="2"><rect x="4" y="5" width="28" height="22"/><path d="M10 22v-6M16 22v-10M22 22v-8"/><circle cx="28" cy="27" r="6"/><path d="M32 31l5 5"/></svg></div>
  </div>
  <div class="service-box" style="top:460px">
    <h3>OPERATIONS &amp; MAINTENANCE</h3>
    <ul><li class="chev">Service &amp; maintenance specifications</li><li class="chev">Policies &amp; procedures</li><li class="chev">Procurement</li></ul>
    <div class="service-icon"><svg width="40" height="40" viewBox="0 0 40 40" fill="none" stroke="#d62b26" stroke-width="2"><rect x="4" y="5" width="30" height="26"/><path d="M4 11h30M9 16h10M9 21h8"/><circle cx="27" cy="25" r="5"/></svg></div>
  </div>
  <a class="btn" style="left:583px;top:684px;width:347px;height:60px">Read more about services</a>
</section>

<h2 class="section-title heading" style="top:2931px"><span>Our team</span></h2>

<div class="arrow" style="left:32px;top:3212px"><svg width="24" height="14" viewBox="0 0 24 14"><path d="M23 7H2M8 1L2 7l6 6" fill="none" stroke="#fff" stroke-width="2"/></svg></div>
<div class="arrow" style="left:1114px;top:3212px"><svg width="24" height="14" viewBox="0 0 24 14"><path d="M1 7h21M16 1l6 6-6 6" fill="none" stroke="#fff" stroke-width="2"/></svg></div>

<div class="team-card" style="left:100px;top:3075px;width:300px">
  <div class="team-photo" role="img" aria-label="Portrait of Dan Harlow"></div>
  <div class="team-name">Dan Harlow</div>
  <div class="team-role">Principal Consultant</div>
  <p class="team-bio">Dan founded Pelu in 2016 and continues to lead the organisation nationally.</p>
</div>
<div class="team-card featured" style="left:437px;top:3034px;width:326px;height:399px;padding-top:26px">
  <div class="team-photo" role="img" aria-label="Portrait of Greg Tanner"></div>
  <div class="team-name">Greg Tanner</div>
  <div class="team-role">Principal Consultant</div>
  <p class="team-bio" style="padding:0 20px">Greg founded Norvane Group in 2016 and joined Pelu as a Director in 2022, taking over leadership of the NSW office.</p>
</div>
<div class="team-card" style="left:800px;top:3055px;width:300px">
  <div class="team-photo" role="img" aria-label="Portrait of Lena Ortiz"></div>
  <div class="team-name">Lena Ortiz</div>
  <div class="team-role">Operations &amp; Administration Coordinator</div>
  <p class="team-bio" style="padding:0 15px">Lena coordinates the operations and administration functions across the business nationally.</p>
</div>

<footer class="site-footer">
  <div class="footer-brand"><span class="brand-square"></span><span class="brand-name">PELU</span></div>
  <div class="socials"><span></span><span></span><span></span></div>
  <h4 class="footer-head" style="left:469px">QUICK LINKS</h4>
  <div class="footer-links">
    <span>HOME</span><span>TEAM</span>
    <span>EXPERIENCE</span><span>ABOUT</span>
    <span>SERVICES</span><span>CONTACT</span>
  </div>
  <h4 class="footer-head" style="left:846px">CONTACT US</h4>
  <ul class="contact-list">
    <li>1300 555 019</li>
    <li>info@pelu.com.au</li>
    <li>PO BOX 9021</li>
    <li>LAKESIDE VIC 3999</li>
  </ul>
  <div class="footer-rule"></div>
  <p class="copyright">©2023 COPYRIGHTS. PELU SERVICES. ALL RIGHTS RESERVED.</p>
</footer>

</body>
</html>
```